Coffee Bag Design for Tollbury Coffee

We’re excited to invite you to help us bring Tollbury Coffee to life on grocery store shelves with a design that embodies our mission of spreading goodness and creating a lasting impact. Tollbury Coffee represents warmth, positivity, and the power of small actions to create ripples of goodness. Each cup not only offers a rich, gourmet coffee experience but also gives back to the community, with $2 from each bag supporting local food banks.

To reflect this vision, we’d love for the design to feature a dark (greyish) blue as the base color to convey depth and quality, complemented by a vibrant light blue that will catch the eye and add energy. Tan or gold accents could add an elegant touch and a feeling of warmth. We are aiming for a look that feels uplifting and engaging, with simplicity and elegance, yet stands out amid other brands on the shelf.

I am attaching the dimension of the bag.

Other information that needs to be listed:
Ingredients: 100% Arabica Coffee
Net Wt. 12 oz. (340 g)
Roasted and distributed by:
Name
Address
email

Text on the back of the bag:
Tollbury Coffee is crafted with a belief that kindness and positivity can spread, touching countless lives with every sip. This gourmet blend delivers a rich taste experience while giving back, as $2 from each bag sold is donated to local food banks to help those in need. Enjoy the warmth and goodness in each cup, knowing you’re making a difference with every purchase.

Thank you!

```html
<!DOCTYPE html>
<html lang="en">
<head>
<meta charset="utf-8">
<title>Tollbury Coffee – Bag Front</title>
<link rel="stylesheet" href="https://fonts.googleapis.com/css2?family=Montserrat:wght@400;500;800&family=Lilita+One&display=swap">
<style>
  :root {
    --stage: #d2d2d2;
    --stage-light: #e2e2e2;
    --slate: #344f5e;
    --sky: #63c9e2;
    --sky-pale: #b9e6f1;
    --gold: #e2a54f;
    --white: #ffffff;
  }
  * { margin: 0; padding: 0; box-sizing: border-box; }
  html, body { width: 1200px; height: 800px; overflow: hidden; }
  body {
    background: radial-gradient(ellipse at center, var(--stage-light), var(--stage));
    font-family: "Montserrat", sans-serif;
    position: relative;
  }
  .bag-front {
    position: absolute;
    left: 300px; top: 40px;
    width: 600px; height: 720px;
    background: var(--slate);
    border-radius: 18px;
    overflow: hidden;
  }
  .gold-frame { position: absolute; left: 0; top: 0; }
  .brand-tab {
    position: absolute;
    left: 222px; top: 51px;
    width: 152px; height: 267px;
    background: var(--sky);
    border-radius: 0 0 76px 76px;
  }
  .cup-art {
    position: absolute;
    left: 22px; top: 104px;
    width: 108px; height: 140px;
    border-radius: 40px 40px 54px 54px;
    background: linear-gradient(180deg, var(--sky-pale), var(--white));
  }
  .brand-name {
    position: absolute;
    left: 76px; top: 350px;
    width: 448px;
    color: var(--white);
    font-weight: 800;
    font-size: 64px;
    line-height: 70px;
  }
  .brand-name span { display: block; }
  .brand-name .line-two { text-align: right; }
  .arabica-badge {
    position: absolute;
    left: 108px; top: 466px;
    width: 112px; height: 112px;
    border: 2px solid var(--gold);
    outline: 1.5px solid var(--gold);
    outline-offset: 4px;
  }
  .badge-text {
    position: absolute;
    inset: 0;
    display: flex; flex-direction: column; align-items: center; justify-content: center;
    font-family: "Lilita One", sans-serif;
    color: var(--sky);
    transform: rotate(-14deg);
    line-height: 1;
  }
  .badge-text .pct { font-size: 25px; }
  .badge-text .word { font-size: 17px; }
  .net-weight {
    position: absolute;
    left: 0; right: 0; top: 614px;
    text-align: center;
    color: var(--white);
    font-size: 19px;
    font-weight: 400;
  }
  .donation {
    position: absolute;
    left: 0; right: 0; top: 650px;
    text-align: center;
    color: var(--gold);
    font-size: 17.5px;
    font-weight: 500;
    letter-spacing: 0.4px;
    white-space: nowrap;
  }
  .donation .amount { font-weight: 800; font-size: 27px; }
</style>
</head>
<body>
  <main class="bag-front">
    <svg class="gold-frame" width="600" height="720" viewBox="0 0 600 720" aria-hidden="true">
      <defs>
        <linearGradient id="frameFade" x1="0" y1="0" x2="0" y2="1">
          <stop offset="0" stop-color="#e2a54f"/>
          <stop offset="0.6" stop-color="#e2a54f" stop-opacity="0.7"/>
          <stop offset="1" stop-color="#e2a54f" stop-opacity="0"/>
        </linearGradient>
      </defs>
      <path d="M66 600 V60 H534 V600" fill="none" stroke="url(#frameFade)" stroke-width="2.5"/>
    </svg>

    <div class="brand-tab">
      <div class="cup-art" role="img" aria-label="White steaming coffee cup illustration"></div>
    </div>

    <h1 class="brand-name">
      <span class="line-one">Tollbury</span>
      <span class="line-two">Coffee</span>
    </h1>

    <div class="arabica-badge">
      <div class="badge-text">
        <span class="pct">100%</span>
        <span class="word">Arabic</span>
        <span class="word">Coffee</span>
      </div>
    </div>

    <p class="net-weight">Net Wt. 12 oz. (340 g)</p>
    <p class="donation"><span class="amount">$2</span> from each sold bag donated to local food banks</p>
  </main>
</body>
</html>
```